Design a website for a quickly growing ghostwriting and editing firm

DWB Productions has a website through Wix, but we need help! We are based in Austin, TX, and we work primarily with self-help, wellness, and diet authors. We offer ghostwriting, editing and book development services. You can see our basic site now at www.dorawhitbyproductions.com

```html
<!DOCTYPE html>
<html lang="en">
<head>
<meta charset="utf-8">
<title>DWB Productions</title>
<link href="https://fonts.googleapis.com/css2?family=Montserrat:wght@400;500;600;700&family=Great+Vibes&display=swap" rel="stylesheet">
<style>
:root{
  --amber:#d08a2e;
  --amber-dark:#b46a14;
  --rust:#9a4d0c;
  --peach:#f7b997;
  --ink:#1f1a17;
  --text:#4a4340;
  --cream:#faf3ee;
  --grey-bg:#f1f1f1;
  --field:#f0f0f0;
  --footer:#3d2211;
  --white:#ffffff;
}
*{margin:0;padding:0;box-sizing:border-box}
html,body{width:1200px;height:4573px;overflow:hidden}
body{font-family:'Montserrat',sans-serif;color:var(--ink);background:var(--white);position:relative}
.abs{position:absolute}
.script{font-family:'Great Vibes',cursive;color:var(--amber-dark);font-size:28px}
.sec-title{font-weight:500;font-size:28px;letter-spacing:.3px;color:var(--ink)}
.rule{width:62px;height:3px;background:var(--amber)}
.center{left:0;width:1200px;text-align:center}

/* header */
.site-header{top:0;left:0;width:1200px;height:98px;background:var(--white)}
.brand{display:flex;align-items:center;gap:12px}
.brand-dot{width:70px;height:70px;border-radius:50%;background:var(--amber)}
.brand-name{font-weight:400;color:var(--amber-dark);font-size:22px;line-height:1.1;letter-spacing:1px}
.nav a{position:absolute;top:36px;font-size:12px;font-weight:500;color:#333;text-decoration:none;letter-spacing:.2px}
.nav a.active{color:var(--amber)}
.nav a.active::after{content:"";position:absolute;left:0;right:0;bottom:-10px;height:2px;background:var(--amber)}

/* hero */
.hero{top:98px;left:0;width:1200px;height:687px;overflow:hidden}
.hero-photo{position:absolute;inset:0;background:linear-gradient(100deg,#f7e9df 0%,#f4ddcc 55%,#efd0bd 100%)}
.hero-kicker{top:212px;left:108px;font-size:20px;letter-spacing:5px;color:#3a2f2a}
.hero-title{top:246px;left:108px;font-size:45px;font-weight:600;line-height:48px;color:#2a1c14}
.btn-fill{display:inline-flex;align-items:center;justify-content:center;border-radius:22px;background:linear-gradient(90deg,var(--amber-dark),var(--amber));color:var(--white);font-weight:700;font-size:12px}
.hero-btn{top:367px;left:108px;width:180px;height:42px}
.arrow{top:280px;width:30px;height:50px}

/* about */
.about-photo{top:796px;left:133px;width:416px;height:416px;border-radius:50%;background:radial-gradient(circle at 50% 45%,#c9c9c9,#6f6a67);border:4px solid var(--amber)}
.about-text{top:955px;left:628px;width:440px;font-size:14px;line-height:27px;color:var(--text)}
.btn-line{display:inline-flex;align-items:center;justify-content:center;border:2px solid var(--amber);border-radius:24px;color:var(--amber-dark);font-weight:700;font-size:13px}

/* why */
.why{top:1320px;left:0;width:1200px;height:545px;background:var(--cream)}
.why-card{top:1485px;width:282px;height:300px;background:var(--white);border-radius:30px 110px 0 30px;box-shadow:0 6px 16px rgba(0,0,0,.06);text-align:center}
.why-icon{margin:48px auto 0;width:100px;height:100px;border-radius:50%;background:var(--amber);border:4px solid var(--white);outline:3px solid var(--amber)}
.why-card.dark .why-icon{background:var(--rust);outline-color:var(--rust)}
.why-card h3{margin-top:36px;font-size:18px;font-weight:500}
.why-card p{margin:8px auto 0;width:200px;font-size:13px;line-height:20px;color:var(--text)}

/* offer */
.offer-photo{border-radius:6px}
.offer-card{border-radius:70px 70px 70px 0;padding:44px 66px;color:var(--white)}
.offer-card h3{font-size:30px;font-weight:400}
.offer-card p{margin-top:14px;font-size:13.5px;line-height:27px}
.offer-card .btn-white{margin-top:20px;display:inline-flex;align-items:center;justify-content:center;width:148px;height:40px;border:2px solid var(--white);border-radius:20px;font-size:11px;font-weight:700}

/* testimonials */
.voices{top:3180px;left:0;width:1200px;height:525px;background:var(--grey-bg)}
.quote-card{top:3340px;width:335px;height:220px;background:var(--white);padding:34px 42px}
.quote-card h4{font-size:13px;font-weight:600;line-height:22px}
.quote-card p{margin-top:8px;font-size:8.5px;line-height:14px;color:var(--text)}
.reviewer{margin-top:12px;display:flex;align-items:center;gap:10px}
.avatar{width:26px;height:26px;border-radius:50%;background:#c8b7c4}
.reviewer b{display:block;font-size:7px}
.stars{color:#f0a21b;font-size:10px;letter-spacing:1px}
.dot{top:3606px;width:12px;height:12px;border-radius:50%;background:var(--ink)}

/* quote form */
.field{left:612px;width:434px;height:40px;background:var(--field);font-size:11px;font-weight:500;padding:12px 26px;color:#333}

/* footer */
.site-footer{top:4280px;left:0;width:1200px;height:293px;background:var(--footer);color:var(--white)}
.foot-h{font-size:14px;font-weight:600;letter-spacing:.5px}
.foot-small{font-size:11px;color:#e6d6c8;line-height:20px}
.vline{width:1px;background:rgba(255,255,255,.18)}
.tick{width:3px;height:18px;background:var(--amber)}
.social{width:24px;height:24px;border-radius:50%;background:var(--white)}
</style>
</head>
<body>

<header class="abs site-header">
  <div class="abs brand" style="top:12px;left:100px">
    <div class="brand-dot"></div>
    <div class="brand-name">DWB<br>PRODUCTIONS</div>
  </div>
  <nav class="nav">
    <a class="active" style="left:423px">ABOUT US</a>
    <a style="left:533px">SERVICES</a>
    <a style="left:640px">GHOST WRITING</a>
    <a style="left:788px">DIET AUTHORS</a>
    <a style="left:927px">BLOGS</a>
    <a style="left:1015px">CONTACT</a>
  </nav>
  <svg class="abs" style="top:34px;left:1105px" width="18" height="18" viewBox="0 0 18 18"><circle cx="7" cy="7" r="5.5" fill="none" stroke="#aaa" stroke-width="1.5"/><line x1="11" y1="11" x2="16" y2="16" stroke="#aaa" stroke-width="1.5"/></svg>
</header>

<section class="abs hero">
  <div class="hero-photo" role="img" aria-label="Calm interior with a pink armchair, side table with plant, and pendant lamp in an arched alcove"></div>
  <div class="abs hero-kicker">DWB PRODUCTIONS</div>
  <h1 class="abs hero-title">SELF HELP WELLNES<br>&amp; DEIT AUTHORS</h1>
  <div class="abs btn-fill hero-btn">GET A QUOTE</div>
  <svg class="abs arrow" style="left:18px" viewBox="0 0 30 50"><polyline points="24,6 6,25 24,44" fill="none" stroke="#9b8f88" stroke-width="3"/></svg>
  <svg class="abs arrow" style="left:1137px" viewBox="0 0 30 50"><polyline points="6,6 24,25 6,44" fill="none" stroke="#9b8f88" stroke-width="3"/></svg>
  <svg class="abs" style="left:0;top:590px" width="1200" height="97" viewBox="0 0 1200 97">
    <path d="M0 97 L0 85 Q600 -30 1200 70 L1200 97 Z" fill="#fff"/>
    <path d="M140 68 Q640 0 1110 52" fill="none" stroke="#c7791f" stroke-width="5"/>
  </svg>
</section>

<section>
  <div class="abs about-photo" role="img" aria-label="Hands typing on a laptop beside glasses and a stack of books"></div>
  <div class="abs script" style="top:845px;left:625px">Who we area</div>
  <h2 class="abs sec-title" style="top:882px;left:626px">ABOUT DWB PRODUCTIONS</h2>
  <div class="abs rule" style="top:925px;left:626px"></div>
  <p class="abs about-text">Lorem Ipsum is simply dummy text of the printing and typeset-ting industry. Lorem Ipsum has been the industry's standard dummy text ever since the 1500s, when an unknown printer took a galley of type and scrambled it to make a type specimen book. It has survived not only five centuries</p>
  <div class="abs btn-line" style="top:1115px;left:626px;width:166px;height:46px">LEARN MORE</div>
</section>

<section class="abs why"></section>
<div class="abs script center" style="top:1362px;font-size:26px">what we do</div>
<h2 class="abs sec-title center" style="top:1398px">WHY DWB PRODUCTIONS</h2>
<div class="abs rule" style="top:1441px;left:569px"></div>
<div class="abs why-card" style="left:158px"><div class="why-icon"></div><h3>SELF HELP</h3><p>Lorem Ipsum is simply dummy text of the printing</p></div>
<div class="abs why-card dark" style="left:462px"><div class="why-icon"></div><h3>WELLNESS</h3><p>Lorem Ipsum is simply dummy text of the printing</p></div>
<div class="abs why-card" style="left:760px"><div class="why-icon"></div><h3>DIET AUTHORS</h3><p>Lorem Ipsum is simply dummy text of the printing</p></div>

<h2 class="abs sec-title center" style="top:1915px">WHAT WE OFFER</h2>
<div class="abs rule" style="top:1957px;left:565px"></div>

<div class="abs offer-photo" style="top:2003px;left:113px;width:504px;height:342px;background:linear-gradient(135deg,#e8e8e8,#9a9a9a 60%,#3a3a3a)" role="img" aria-label="Close-up of a typewriter striking the word ghostwriting"></div>
<div class="abs offer-card" style="top:2040px;left:557px;width:491px;height:267px;background:var(--amber)"><h3>Ghost writing</h3><p>Lorem Ipsum is simply dummy text of the printing and typesetting industry. Lorem Ipsum has been the indus-try's standard dummy text ever since</p><span class="btn-white">LEARN MORE</span></div>

<div class="abs offer-photo" style="top:2395px;left:557px;width:493px;height:315px;background:linear-gradient(135deg,#5a3b24,#8b6140 55%,#c9b49b)" role="img" aria-label="Overhead view of a desk with a computer showing photos, notes and a coffee cup"></div>
<div class="abs offer-card" style="top:2418px;left:106px;width:490px;height:267px;background:var(--peach)"><h3>Book Editing</h3><p>Lorem Ipsum is simply dummy text of the printing and typesetting industry. Lorem Ipsum has been the industry's standard dummy text ever since</p><span class="btn-white">LEARN MORE</span></div>

<div class="abs offer-photo" style="top:2762px;left:113px;width:509px;height:335px;background:linear-gradient(135deg,#d9d3cc,#a08f80 55%,#5e4a3a)" role="img" aria-label="Writer taking notes with a pen at a wooden table beside a cup"></div>
<div class="abs offer-card" style="top:2795px;left:564px;width:492px;height:268px;background:var(--rust)"><h3>Book development</h3><p>Lorem Ipsum is simply dummy text of the printing and typesetting industry. Lorem Ipsum has been the indus-try's standard dummy text ever since</p><span class="btn-white">LEARN MORE</span></div>

<section class="abs voices"></section>
<h2 class="abs sec-title center" style="top:3246px">WHAT PEOPLE SAYS</h2>
<div class="abs rule" style="top:3293px;left:573px"></div>
<div class="abs quote-card" style="left:94px"><h4>What PlotGuide Guides Experienced After Getting Certified</h4><p>Working with Marla was easy and exciting. She was able to distill our ideas and keep us focused on what we needed for our website. She was able to speak to us in simple language on the details and operations of our website.</p><div class="reviewer"><div class="avatar"></div><div><b>ELLIS CRANE</b><span class="stars">★★★★★</span></div></div></div>
<div class="abs quote-card" style="left:455px"><h4>What PlotGuide Guides Experienced After Getting Certified</h4><p>Working with Marla was easy and exciting. She was able to distill our ideas and keep us focused on what we needed for our website. She was able to speak to us in simple language on the details and operations of our website.</p><div class="reviewer"><div class="avatar"></div><div><b>ELLIS CRANE</b><span class="stars">★★★★★</span></div></div></div>
<div class="abs quote-card" style="left:816px"><h4>What PlotGuide Guides Experienced After Getting Certified</h4><p>Working with Marla was easy and exciting. She was able to distill our ideas and keep us focused on what we needed for our website. She was able to speak to us in simple language on the details and operations of our website.</p><div class="reviewer"><div class="avatar"></div><div><b>ELLIS CRANE</b><span class="stars">★★★★★</span></div></div></div>
<div class="abs dot" style="left:563px;background:var(--amber)"></div>
<div class="abs dot" style="left:584px"></div>
<div class="abs dot" style="left:605px"></div>

<svg class="abs" style="top:3745px;left:105px" width="450" height="495" viewBox="0 0 450 495">
  <polygon points="225,4 446,128 446,367 225,491 4,367 4,128" fill="#f6e6d6" stroke="#f1d7bd" stroke-width="6" stroke-linejoin="round"/>
  <polygon points="225,30 422,142 422,353 225,465 28,353 28,142" fill="#d9a064"/>
</svg>
<div class="abs" style="top:3790px;left:147px;width:366px;height:415px;clip-path:polygon(50% 0,100% 26%,100% 74%,50% 100%,0 74%,0 26%);background:linear-gradient(135deg,#f3f3f3,#b9b9b9)" role="img" aria-label="Hands typing on a laptop keyboard"></div>

<div class="abs script" style="top:3792px;left:612px">Get in touch</div>
<h2 class="abs sec-title" style="top:3828px;left:612px">GET A FREE QUOTE</h2>
<div class="abs rule" style="top:3870px;left:612px"></div>
<div class="abs field" style="top:3898px">YOUR NAME *</div>
<div class="abs field" style="top:3952px">E-MAIL *</div>
<div class="abs field" style="top:4002px">PHONE *</div>
<div class="abs field" style="top:4052px;height:88px">LEAVE MESSAGE</div>
<div class="abs btn-fill" style="top:4153px;left:617px;width:173px;height:44px;background:var(--amber-dark)">SUBMIT MESSAGE</div>

<footer class="abs site-footer">
  <div class="abs brand" style="top:46px;left:96px">
    <div class="brand-dot" style="width:66px;height:66px"></div>
    <div class="brand-name" style="color:#e8d7c6">DWB<br>PRODUCTIONS</div>
  </div>
  <div class="abs foot-small" style="top:150px;left:98px;font-size:9px;line-height:16px">Copyright 2021 DWB Productions All Right Reserved<br>Privacy Policy &nbsp;|&nbsp; Contact</div>
  <div class="abs vline" style="top:0;left:415px;height:293px"></div>
  <div class="abs vline" style="top:0;left:700px;height:293px"></div>
  <div class="abs vline" style="top:0;left:885px;height:293px"></div>
  <div class="abs tick" style="top:58px;left:415px"></div>
  <div class="abs tick" style="top:58px;left:700px"></div>
  <div class="abs tick" style="top:58px;left:885px"></div>

  <div class="abs foot-h" style="top:58px;left:469px">CONTACT US</div>
  <svg class="abs" style="top:98px;left:467px" width="18" height="24" viewBox="0 0 18 24"><path d="M9 1C4.6 1 1.5 4.2 1.5 8.3 1.5 14 9 22.5 9 22.5S16.5 14 16.5 8.3C16.5 4.2 13.4 1 9 1Z" fill="none" stroke="#fff" stroke-width="1.6"/><circle cx="9" cy="8.5" r="2.8" fill="none" stroke="#fff" stroke-width="1.6"/></svg>
  <div class="abs foot-small" style="top:96px;left:496px">88 Juniper Row, Austin<br>TX 78704</div>
  <svg class="abs" style="top:146px;left:468px" width="18" height="18" viewBox="0 0 24 24"><path d="M5 2h4l2 5-3 2c1.3 2.8 3.2 4.7 6 6l2-3 5 2v4c0 1.1-.9 2-2 2C10 20 4 14 3 4c0-1.1.9-2 2-2Z" fill="none" stroke="#fff" stroke-width="1.6"/></svg>
  <div class="abs foot-small" style="top:145px;left:496px">1-512-555-0148</div>
  <svg class="abs" style="top:184px;left:467px" width="20" height="16" viewBox="0 0 20 16"><rect x="1" y="1" width="18" height="14" fill="none" stroke="#fff" stroke-width="1.5"/><polyline points="1,1 10,9 19,1" fill="none" stroke="#fff" stroke-width="1.5"/></svg>
  <div class="abs foot-small" style="top:182px;left:496px">marla@northlightstudio.com</div>

  <div class="abs foot-h" style="top:60px;left:738px;font-size:12px">COMPANY</div>
  <div class="abs foot-small" style="top:84px;left:738px">About us<br>Services<br>Ghost writing<br>Diet authors<br>Blogs<br>Contact</div>

  <div class="abs foot-h" style="top:58px;left:926px">FOLLOW US</div>
  <div class="abs social" style="top:88px;left:926px"></div>
  <div class="abs social" style="top:88px;left:955px"></div>
  <div class="abs social" style="top:88px;left:984px"></div>
</footer>

</body>
</html>
```